Realty Group Needs Classy, Contemporary Letterhead Design

We need a letterhead design for a new realty company located in NY, USA. We buy investment properties to rehabilitate and or keep in our rental portfolio.

```html
<!DOCTYPE html>
<html lang="en">
<head>
<meta charset="utf-8">
<title>Meridian Realty Group — Letterhead</title>
<link rel="stylesheet" href="https://fonts.googleapis.com/css2?family=Open+Sans:wght@400;600;800&family=Sacramento&display=swap">
<style>
  :root {
    --backdrop: #b9b9bb;
    --paper: #ffffff;
    --brand-purple: #4a2a8e;
    --rule-grey: #8e8e92;
    --text-grey: #8a8a8f;
    --text-dark: #6e6e74;
    --on-brand: #ffffff;
  }
  * { box-sizing: border-box; margin: 0; padding: 0; }
  html, body { width: 1200px; height: 795px; overflow: hidden; }
  body {
    background: var(--backdrop);
    font-family: "Open Sans", Arial, sans-serif;
    position: relative;
  }
  .letterhead {
    position: absolute;
    left: 330px; top: 18px;
    width: 540px; height: 759px;
    background: var(--paper);
    box-shadow: 0 2px 10px rgba(0,0,0,.12);
    overflow: hidden;
    color: var(--text-grey);
  }
  .brand {
    position: absolute; left: 46px; top: 48px;
    display: flex; align-items: center; gap: 8px;
  }
  .brand-dot {
    width: 22px; height: 22px; border-radius: 50%;
    background: var(--brand-purple);
  }
  .brand-name {
    font-weight: 800; font-size: 24px; letter-spacing: .5px;
    color: var(--brand-purple); line-height: 1;
  }
  .brand-sub {
    font-weight: 800; font-size: 8px; letter-spacing: 1.2px;
    color: var(--brand-purple); margin-top: 3px;
  }
  .contact-list {
    position: absolute; right: 44px; top: 44px;
    list-style: none; font-size: 7.5px; line-height: 12px;
    color: var(--text-dark);
  }
  .contact-list li { display: flex; align-items: center; gap: 5px; }
  .contact-icon { width: 8px; height: 8px; }
  .letter-body {
    position: absolute; left: 46px; top: 150px; width: 450px;
    font-size: 8.5px; line-height: 12px;
  }
  .letter-date { margin-bottom: 16px; }
  .recipient { margin-bottom: 12px; }
  .salutation { font-weight: 600; color: var(--text-dark); font-size: 10px; margin-bottom: 12px; }
  .letter-body p.para { margin-bottom: 14px; text-align: justify; }
  .sign-off {
    position: absolute; right: 46px; top: 458px;
    text-align: right; font-size: 8.5px; line-height: 12px;
  }
  .signature {
    font-family: "Sacramento", cursive;
    font-size: 30px; color: var(--text-grey); line-height: 34px; margin: 2px 0;
  }
  .footer-band { position: absolute; left: 0; bottom: 0; width: 540px; height: 200px; }
  .footer-address {
    position: absolute; right: 18px; bottom: 14px;
    color: var(--on-brand); font-size: 9px; display: flex; align-items: center; gap: 5px;
  }
  .footer-address strong { font-weight: 800; }
</style>
</head>
<body>
  <main class="letterhead">
    <header class="brand">
      <span class="brand-dot"></span>
      <div>
        <div class="brand-name">MERIDIAN</div>
        <div class="brand-sub">REALTY GROUP, LLC</div>
      </div>
    </header>

    <ul class="contact-list">
      <li><svg class="contact-icon" viewBox="0 0 10 10"><circle cx="5" cy="5" r="5" fill="#6e6e74"/><path d="M3.3 2.6l1 1-.5.6c.4.8 1 1.4 1.8 1.8l.6-.5 1 1-.7.9C4.6 7.2 2.8 5.4 2.4 3.3z" fill="#fff"/></svg>(555) 014-2290</li>
      <li><svg class="contact-icon" viewBox="0 0 10 10"><circle cx="5" cy="5" r="5" fill="#6e6e74"/><rect x="3" y="2.5" width="4" height="5" rx=".6" fill="#fff"/></svg>(555) 014-2291</li>
      <li><svg class="contact-icon" viewBox="0 0 10 10"><circle cx="5" cy="5" r="5" fill="#6e6e74"/><rect x="2.5" y="3.2" width="5" height="3.6" fill="#fff"/><path d="M2.5 3.2L5 5.2l2.5-2" stroke="#6e6e74" stroke-width=".6" fill="none"/></svg>hello@meridianrealty.example</li>
      <li><svg class="contact-icon" viewBox="0 0 10 10"><circle cx="5" cy="5" r="5" fill="#6e6e74"/><circle cx="5" cy="5" r="2.6" stroke="#fff" stroke-width=".7" fill="none"/><path d="M2.4 5h5.2" stroke="#fff" stroke-width=".6"/></svg>www.meridianrealty.example</li>
    </ul>

    <section class="letter-body">
      <p class="letter-date">January 03, 2017</p>
      <p class="recipient">Mr. John Doe<br>President<br>AA Corporation<br>111 Street Name, Suite#<br>City, State, 12345</p>
      <p class="salutation">Dear Mr. John,</p>
      <p class="para">Lorem Ipsum is simply dummy text of the printing and typesetting industry. Lorem Ipsum has been the industry's standard dummy text ever since the 1500s, when an unknown printer took a galley of type and scrambled it to make a type specimen book. It has survived not only five centuries, but also the leap into electronic typesetting, remaining essentially unchanged.</p>
      <p class="para">The standard chunk of Lorem Ipsum used since the 1500s is reproduced below for those interested. Sections 1.10.32 and 1.10.33 from "de Finibus Bonorum et Malorum" by Cicero are also reproduced in their exact original form, accompanied by English versions from the 1914 translation by H. Rackham.</p>
      <p class="para">Lorem Ipsum is simply dummy text of the printing and typesetting industry. Lorem Ipsum has been the industry's standard dummy text ever since the 1500s, when an unknown printer took a galley of type and scrambled it to make a type specimen book. It has survived not only five centuries, but also the leap into electronic typesetting, remaining essentially unchanged. It was popularised in the</p>
    </section>

    <section class="sign-off">
      <p>Sincerely Your,</p>
      <p class="signature">your name</p>
      <p>Name Last Name<br>Company Name</p>
    </section>

    <svg class="footer-band" viewBox="0 0 540 200" preserveAspectRatio="none" aria-hidden="true">
      <path d="M0 196 C 260 184, 430 120, 540 22" stroke="var(--rule-grey)" stroke-width="3" fill="none"/>
      <path d="M0 200 L0 199 C 262 190, 434 128, 540 32 L540 200 Z" fill="var(--brand-purple)"/>
    </svg>
    <p class="footer-address">
      <svg width="9" height="9" viewBox="0 0 10 10"><circle cx="5" cy="5" r="5" fill="#d9d3ea"/><path d="M5 2.2a1.9 1.9 0 0 0-1.9 1.9C3.1 5.5 5 7.8 5 7.8s1.9-2.3 1.9-3.7A1.9 1.9 0 0 0 5 2.2z" fill="var(--brand-purple)"/></svg>
      <span><strong>VEGA</strong> : Suite 102 Street name, State, Zip 2034, Country</span>
    </p>
  </main>
</body>
</html>
```